Home Staging Company needs business card design

We're a home staging company called Brightly Settled Home Staging. We would like a business card design that includes aqua and gray. Our current logo of house within chair is fine but I find we almost always use the logo in one color. I'll upload images of front and back of our current card and our logo. Note that we have dropped "Solutions" from our company name and don't want to include it on the card.

Target Market(s)

Realtors and homeowners - people interested in selling their homes

Contact Information for Business Card

Marisol Thistlewood
Brightly Settled Home Staging
757-555-0193
www.brightlysettled.com
marisol@brightlysettled.com

Font styles to use
Serif
Script

Requirements
Must have
• My logo and contact details
• UPDATE***
• I forgot to say that the company name should be included on the front of the card somehow.

```html
<!DOCTYPE html>
<html lang="en">
<head>
<meta charset="utf-8">
<title>Brightly Settled Home Staging – Business Card</title>
<link href="https://fonts.googleapis.com/css2?family=Roboto:wght@400&family=Questrial&family=Playfair+Display:wght@500&display=swap" rel="stylesheet">
<style>
  :root {
    --canvas: #bdbdbd;
    --card-front: #ededed;
    --card-front-edge: #e2e2e2;
    --card-back: #363a3d;
    --ink: #2f3336;
    --ink-soft: #44484b;
    --aqua: #4a9fae;
    --on-dark: #e9eaeb;
    --faint-light: rgba(0, 0, 0, 0.045);
    --faint-dark: rgba(255, 255, 255, 0.05);
  }
  * { box-sizing: border-box; margin: 0; padding: 0; }
  html, body {
    width: 1200px; height: 576px; overflow: hidden;
    background: var(--canvas);
  }
  .canvas { position: relative; width: 1200px; height: 576px; }

  .card {
    position: absolute; top: 138px;
    width: 485px; height: 294px;
    border-radius: 14px; overflow: hidden;
  }
  .card--front {
    left: 82px;
    background: linear-gradient(135deg, var(--card-front) 0%, var(--card-front-edge) 100%);
  }
  .card--back { left: 602px; background: var(--card-back); }

  .emblem-area { position: absolute; border-radius: 50%; }
  .card--front .emblem-area {
    left: 310px; top: -10px; width: 210px; height: 210px;
    background: var(--faint-light);
  }
  .card--back .emblem-area {
    left: -70px; top: -20px; width: 210px; height: 210px;
    background: var(--faint-dark);
  }

  .person { position: absolute; left: 27px; top: 34px; }
  .person__name {
    font-family: "Roboto", sans-serif; font-weight: 400;
    font-size: 19px; color: var(--ink); letter-spacing: 0.1px;
  }
  .person__name .surname { color: var(--aqua); }
  .person__title {
    margin-top: 5px;
    font-family: "Questrial", sans-serif; font-size: 11px; color: var(--ink-soft);
  }

  .contacts { position: absolute; left: 27px; top: 101px; list-style: none; }
  .contacts li {
    display: flex; align-items: center; gap: 10px; height: 17px;
    font-family: "Questrial", sans-serif; font-size: 12px; color: var(--ink);
  }
  .contacts svg { width: 10px; height: 10px; fill: var(--aqua); flex: none; }

  .brand { position: absolute; display: flex; align-items: center; gap: 9px; }
  .card--front .brand { left: 27px; top: 224px; }
  .card--back .brand { left: 222px; top: 222px; }
  .brand__mark { width: 12px; height: 12px; border-radius: 50%; background: var(--aqua); }
  .brand__name {
    font-family: "Playfair Display", serif; font-weight: 500; font-size: 16px;
  }
  .card--front .brand__name { color: var(--ink); }
  .card--back .brand__name { color: var(--on-dark); }
</style>
</head>
<body>
<main class="canvas">
  <section class="card card--front" aria-label="Card front">
    <div class="emblem-area" role="img" aria-label="Faint oversized brand emblem decoration"></div>

    <div class="person">
      <p class="person__name">Marisol <span class="surname">Thistlewood</span></p>
      <p class="person__title">Managing Director</p>
    </div>

    <ul class="contacts">
      <li>
        <svg viewBox="0 0 10 10" aria-hidden="true"><path d="M1 2.2C1 1.5 1.6 1 2.6 1h4.8C8.4 1 9 1.5 9 2.2V3.3H7V2.5H3v.8H1zM2.5 4h5l1.3 4.2c.1.4-.2.8-.6.8H1.8c-.4 0-.7-.4-.6-.8zM5 5.2a1.1 1.1 0 1 0 0 2.2 1.1 1.1 0 0 0 0-2.2z"/></svg>
        757-555-0193
      </li>
      <li>
        <svg viewBox="0 0 10 10" aria-hidden="true"><path d="M5 .5a4.5 4.5 0 1 0 0 9 4.5 4.5 0 0 0 0-9zm0 1c.5 0 1.1 1 1.3 2.6H3.7C3.9 2.5 4.5 1.5 5 1.5zM1.6 4.6h1.6v.8H1.6zm2.1 0h2.6v.8H3.7zm3.1 0h1.6v.8H6.8zM3.7 5.9h2.6C6.1 7.5 5.5 8.5 5 8.5S3.9 7.5 3.7 5.9z"/></svg>
        www.brightlysettled.com
      </li>
      <li>
        <svg viewBox="0 0 10 10" aria-hidden="true"><path d="M.5 2h9v6h-9zM1.3 2.6 5 5.6l3.7-3H1.3z"/></svg>
        marisol@brightlysettled.com
      </li>
    </ul>

    <div class="brand">
      <span class="brand__mark" aria-hidden="true"></span>
      <span class="brand__name">Brightly Settled Home Staging</span>
    </div>
  </section>

  <section class="card card--back" aria-label="Card back">
    <div class="emblem-area" role="img" aria-label="Faint oversized brand emblem decoration"></div>
    <div class="brand">
      <span class="brand__mark" aria-hidden="true"></span>
      <span class="brand__name">Brightly Settled Home Staging</span>
    </div>
  </section>
</main>
</body>
</html>
```